Powerpoint, Graphics for Sermon Series

I am starting a sermon series on the short letters if Scripture that are between Hebrews and Revelation. The sermon series will be called "Walking Unmarked Trails: Lasting Lessons from Quiet Hills."

Think about finding a packet of letters in an Attic. There is only the dialogue of the writer. We don't know exactly what the receivers were going through or even what their response to the letters were/are!

Target Market(s)

Local Church

Industry/Entity Type

Christian

Font styles to use
Serif
Sans Serif

Colors

Designer to choose colors to be used in the design.

Requirements
Must have
• Powerpoint Slide with Title -
• Background Slide -
• It would be great to have both JPG, PNG, and Photoshop/Indesign that can be used for powerpoint, both in 4x3 ration and wide... Need Title Slide with typography and background slide for text to go over the top of.
• Stick with the theme -- Walking Unmarked Trails
• I am including our church logo, but don't feel like you need to use it in anyway.
Nice to have
• Social Media Slides - Square Slide, Facebook Header
• Greyscale Version?

```html
<!DOCTYPE html>
<html lang="en">
<head>
<meta charset="utf-8">
<title>Walking Unmarked Trails: Lasting Lessons from Quiet Hills</title>
<link href="https://fonts.googleapis.com/css2?family=Roboto+Slab:wght@500;600;700&display=swap" rel="stylesheet">
<style>
  :root {
    --paper: #ffffff;
    --mist: #ebe6e1;
    --parchment: #e2c596;
    --parchment-deep: #c99d62;
    --wood-mid: #8f6440;
    --wood-dark: #4f331d;
    --accent-orange: #f49b14;
    --title-brown: #5b3b22;
    --church-brown: #6b4a2e;
  }
  html, body {
    margin: 0;
    padding: 0;
    overflow: hidden;
    background: var(--paper);
  }
  .slide {
    position: relative;
    width: 1200px;
    height: 900px;
    overflow: hidden;
    background: var(--paper);
  }
  .slide-art {
    position: absolute;
    inset: 0;
    display: block;
  }
  .series-title {
    position: absolute;
    right: 28px;
    top: 378px;
    margin: 0;
    text-align: right;
    font-family: "Roboto Slab", Georgia, serif;
    font-weight: 600;
    font-size: 38px;
    line-height: 57px;
    letter-spacing: 0.2px;
    color: var(--title-brown);
  }
  .series-title span {
    display: block;
    white-space: nowrap;
  }
  .church-name {
    position: absolute;
    right: 28px;
    top: 730px;
    display: flex;
    align-items: center;
    gap: 16px;
    font-family: "Roboto Slab", Georgia, serif;
    font-weight: 600;
    font-size: 32px;
    line-height: 1.15;
    color: var(--church-brown);
    text-align: right;
  }
  .church-mark {
    width: 22px;
    height: 22px;
    background: var(--church-brown);
    flex: none;
  }
</style>
</head>
<body>
<main class="slide">
  <svg class="slide-art" width="1200" height="900" viewBox="0 0 1200 900">
    <defs>
      <linearGradient id="mist-fill" x1="0" y1="0" x2="1" y2="1">
        <stop offset="0" stop-color="#ffffff"/>
        <stop offset="0.6" stop-color="#f5f2ef"/>
        <stop offset="1" stop-color="#ebe6e1"/>
      </linearGradient>
      <linearGradient id="wood-fill" x1="0" y1="0" x2="0.6" y2="1">
        <stop offset="0" stop-color="#8a6440"/>
        <stop offset="0.5" stop-color="#7a5433"/>
        <stop offset="1" stop-color="#4f331d"/>
      </linearGradient>
      <radialGradient id="parchment-glow" cx="0.4" cy="0.5" r="0.55">
        <stop offset="0" stop-color="#e6cb9c" stop-opacity="1"/>
        <stop offset="0.5" stop-color="#c99d62" stop-opacity="0.85"/>
        <stop offset="1" stop-color="#c99d62" stop-opacity="0"/>
      </radialGradient>
    </defs>
    <rect class="backdrop" x="0" y="0" width="1200" height="900" fill="url(#mist-fill)" role="img" aria-label="Faint hillside with three crosses under a pale sky"/>
    <path class="accent-band" d="M0,0 L622,0 C530,250 530,610 700,900 L0,900 Z" fill="#f49b14"/>
    <path class="accent-gap" d="M0,0 L604,0 C512,250 512,610 682,900 L0,900 Z" fill="#ffffff"/>
    <g class="letters-photo" role="img" aria-label="Old handwritten letters with an antique iron key on a wooden table">
      <path d="M0,0 L597,0 C505,250 505,610 674,900 L0,900 Z" fill="url(#wood-fill)"/>
      <path d="M0,0 L597,0 C505,250 505,610 674,900 L0,900 Z" fill="url(#parchment-glow)"/>
    </g>
  </svg>

  <h1 class="series-title">
    <span>Walking Unmarked Trails</span>
    <span>Lasting Lessons from Quiet Hills</span>
  </h1>

  <div class="church-name">
    <span class="church-mark"></span>
    <span>Cedar Ridge<br>Community Church</span>
  </div>
</main>
</body>
</html>
```